Killer Webpage Design

I currently have a self-hosted webpage through wordpress at www.velmarqstudio.com - the content is complete and I'm happy with this but I need it designed (no coding) to complete my requirements. I'm happy to take designs which are non-Wordpress if there is specific advantage in this.

My full branding logos are attached along with color files. My main aim is consistent branding across all areas (social media, business cards, emails, websites). I have the rest running but am not happy with the available default selections from Wordpress.

I would prefer to use the darker blue version of the logo as I feel this has more standout in online media, however I would appreciate submissions with both variants to help me choose.

With the homepage I will also want to see blog pages and category pages designed but this can come after I have selected a design to go with,

Sites that I like and are related to my business include the following:
http://www.brindlepath.com/au/accounting-software/
http://www.tasklanternpro.com/home.aspx
https://pelicoin.com/register
Updates

Apologies for the confusion - to clarify for designers I am looking for design only, no coding.

FYI - i have now uploaded business cards for an idea of the contemporary style of design completed so far.

Target Market(s)

small to medium business. Not systemised but looking for help and support.

Industry/Entity Type

Business

Requirements
Must have
• I'm looking for a minimalist professional page, with the ability to easily add new sections when required. I will also need a CMS to add blog posts on the go, with the same features that it currently has (comments, social logon etc)

```html
<!DOCTYPE html>
<html lang="en">
<head>
<meta charset="utf-8">
<title>Velmarq Studio</title>
<link rel="stylesheet" href="https://fonts.googleapis.com/css2?family=PT+Sans:wght@400;700&display=swap">
<style>
:root{
  --header-dark:#021a25;
  --header-mid:#0a3547;
  --nav-teal:#1ab0c6;
  --nav-teal-dark:#128ea3;
  --nav-active:#0f7f94;
  --heading-red:#a01f26;
  --heading-orange:#cf5d1c;
  --button-orange:#dd6420;
  --button-orange-dark:#b94c12;
  --link-blue:#1c5a83;
  --body-text:#333;
  --page-bg:#f4f4f4;
  --band-bg:#e9e9e9;
  --footer-bg:#2c2c2c;
  --footer-text:#d8d8d8;
}
*{box-sizing:border-box;margin:0;padding:0}
html,body{width:908px;height:1200px;overflow:hidden}
body{font-family:"PT Sans",sans-serif;color:var(--body-text);background:var(--page-bg);position:relative}
.abs{position:absolute}

/* header */
.site-header{position:absolute;left:0;top:0;width:908px;height:90px;background:linear-gradient(var(--header-mid),var(--header-dark))}
.brand{position:absolute;left:77px;top:26px;display:flex;align-items:center;gap:9px;color:#fff;font-size:25px;font-weight:700;letter-spacing:-.3px}
.brand-dot{width:30px;height:30px;border-radius:50%;background:var(--nav-teal)}
.search-box{position:absolute;left:610px;top:34px;width:160px;height:22px;background:#fff;font-size:11px;color:#555;padding:4px 12px}
.search-box svg{position:absolute;right:7px;top:4px}
.lang-select{position:absolute;left:776px;top:34px;width:65px;height:22px;background:#fff;font-size:10px;color:#555;padding:4px 0 0 8px;display:flex;gap:5px}
.lang-flag{width:12px;height:8px;background:#c8283a;margin-top:3px}
.lang-select svg{margin-top:5px;margin-left:6px}

/* nav */
.main-nav{position:absolute;left:0;top:90px;width:908px;height:41px;background:linear-gradient(var(--nav-teal),var(--nav-teal-dark));display:flex;padding-left:68px}
.main-nav a{color:#fff;text-decoration:none;font-size:12.5px;line-height:41px;padding:0 11.5px;border-right:1px solid rgba(0,0,0,.15);text-shadow:0 1px 1px rgba(0,0,0,.3)}
.main-nav a.active{background:var(--nav-active);padding:0 13.5px}

/* hero */
.hero{position:absolute;left:0;top:131px;width:908px;height:239px;background:linear-gradient(180deg,#5d8cae 0%,#7fa9c7 55%,#c9d8e3 100%)}
.hero-art{position:absolute;left:120px;top:18px;width:220px;height:221px;border-radius:110px 110px 0 0;background:radial-gradient(circle at 45% 40%,#9fc4dd,#3f6f93 70%,transparent 71%)}
.hero-panel{position:absolute;left:409px;top:33px;width:432px;height:178px;background:rgba(20,40,55,.72);padding:13px 30px}
.hero-panel h1{color:#fff;font-size:18.5px;line-height:26px;font-weight:700}
.hero-panel p{color:#eef;font-size:11.5px;line-height:17.5px;margin-top:7px}
.demo-btn{display:inline-flex;align-items:center;gap:7px;margin-top:14px;background:#fff;border-radius:3px;padding:7px 10px;font-size:16px;color:#333}
.demo-btn b{font-weight:700}
.demo-btn i{display:block;width:17px;height:17px;border-radius:50%;background:#666;position:relative}
.demo-btn i:after{content:"";position:absolute;left:6px;top:5px;width:4px;height:4px;border-top:2px solid #fff;border-right:2px solid #fff;transform:rotate(45deg)}

/* welcome */
.section-title{color:var(--heading-red);font-size:19.5px;font-weight:700;line-height:23px}
.copy{font-size:11px;line-height:17.4px}
.copy p+p{margin-top:7px}
.btn{position:absolute;display:block;height:30px;background:linear-gradient(#ec7b32,var(--button-orange-dark));border-radius:3px;color:#fff;font-size:12px;line-height:30px;text-align:center;text-shadow:0 1px 1px rgba(0,0,0,.35)}
.welcome{position:absolute;left:0;top:370px;width:908px;height:535px;background:linear-gradient(#ececec,#fafafa 40%,#f6f6f6)}
.video{position:absolute;left:599px;top:60px;width:241px;height:151px;border-radius:3px;background:radial-gradient(circle at 50% 40%,#4a6a86,#1e3144 80%);display:flex;align-items:center;justify-content:center}
.rule{position:absolute;left:69px;top:244px;width:771px;height:1px;background:#c8c8c8}
.service-title{position:absolute;top:268px;font-size:19px;font-weight:700;color:var(--heading-red);line-height:21px}
.service-title.orange{color:var(--heading-orange)}
.service-list{position:absolute;left:599px;top:329px;width:241px;list-style:none}
.service-list li{height:34px;margin-bottom:1.5px;background:linear-gradient(#f3f3f3,#e6e6e6);border:1px solid #d6d6d6;display:flex;align-items:center;padding-left:15px;gap:20px;color:var(--link-blue);font-size:14.5px;font-weight:700}
.chev{width:15px;height:15px;background:#fff;border:1px solid #d3d3d3;position:relative}
.chev:after{content:"";position:absolute;left:3px;top:4px;width:4px;height:4px;border-top:1.5px solid #555;border-right:1.5px solid #555;transform:rotate(45deg)}

/* blog */
.blog{position:absolute;left:0;top:905px;width:908px;height:209px;background:var(--band-bg);border-top:1px solid #d8d8d8}
.blog-arrows{position:absolute;left:816px;top:18px}
.blog-image{position:absolute;left:69px;top:52px;width:241px;height:136px;border-radius:3px;background:radial-gradient(circle at 50% 35%,#4f8af0,#10249a 60%,#07103f)}
.post-title{position:absolute;left:335px;top:58px;font-size:14.5px;color:var(--link-blue)}
.post-meta{position:absolute;left:335px;top:77px;font-size:10px;color:#333}
.post-body{position:absolute;left:335px;top:99px;width:506px;text-align:justify}
.share-row{position:absolute;left:333px;top:171px;display:flex;gap:6px;font-size:9px}
.share-btn{display:flex;align-items:center;gap:3px;height:15px;padding:0 4px;background:#f5f5f5;border:1px solid #c8c8c8;border-radius:2px;color:#3b5998}
.share-btn span{width:9px;height:9px;background:#7a93c2}
.share-count{height:15px;padding:0 4px;border:1px solid #c8c8c8;background:#fff;line-height:13px;color:#333}

/* footer */
.site-footer{position:absolute;left:0;top:1114px;width:908px;height:86px;background:var(--footer-bg)}
.footer-nav{position:absolute;left:69px;top:23px;font-size:11px;color:var(--footer-text)}
.footer-nav span{margin:0 8px}
.copyright{position:absolute;left:69px;top:51px;font-size:11px;color:var(--footer-text);word-spacing:2px}
.social{position:absolute;left:799px;top:33px;display:flex;gap:5px}
.social i{display:block;width:18px;height:18px;border-radius:3px}
</style>
</head>
<body>

<header class="site-header">
  <div class="brand"><span class="brand-dot"></span>Velmarq Studio</div>
  <div class="search-box">Search
    <svg width="12" height="12" viewBox="0 0 12 12"><circle cx="4.5" cy="4.5" r="3.5" fill="none" stroke="#222" stroke-width="1.8"/><path d="M7 7l4 4" stroke="#222" stroke-width="2.4"/></svg>
  </div>
  <div class="lang-select"><span class="lang-flag"></span>Eng
    <svg width="7" height="5" viewBox="0 0 7 5"><path d="M0 0h7L3.5 5z" fill="#555"/></svg>
  </div>
</header>

<nav class="main-nav">
  <a class="active">Home</a><a>Software Training and Implementation</a><a>Project Management</a><a>Business Process Analysis</a><a>Blog</a><a>About Us</a><a>Contact Us</a>
</nav>

<section class="hero">
  <div class="hero-art" role="img" aria-label="Glass globe on a pedestal against a blue sky with clouds"></div>
  <div class="hero-panel">
    <h1>Curabitur non massa vestibulum, egestas velit vitae, imperdiet velit.</h1>
    <p>Aliquam interdum sollicitudin odio. Mauris nunc ante, sagittis id porta quis, semper non neque. Suspendisse ac pulvinar tellus.</p>
    <span class="demo-btn"><b>FREE</b> Demo <i></i></span>
  </div>
</section>

<section class="welcome">
  <h2 class="section-title abs" style="left:69px;top:24px">Welcome to Velmarq Studio</h2>
  <div class="copy abs" style="left:69px;top:58px;width:504px;text-align:justify">
    <p>Cloud computing spending is due to account for a third of annual IT expenditure growth by the end of 2013. Every year the range of cloud software systems gets bigger, now including Brindlepath Accounting, Cloudwell Suite for Business, Jobmarrow Job Management Software, Deskfold 365, Plancrest Project Manager and many more.</p>
    <p>Signing up for cloud software is only the first part of the process, and then it has to be implemented into your business. That's where Velmarq Studio comes in.</p>
  </div>
  <span class="btn" style="left:69px;top:183px;width:81px">VIEW MORE</span>
  <div class="video" role="img" aria-label="Video preview: cloud outline above an open hand">
    <svg width="58" height="58" viewBox="0 0 58 58"><circle cx="29" cy="29" r="26" fill="none" stroke="#fff" stroke-width="4"/><path d="M22 16l20 13-20 13z" fill="#fff"/></svg>
  </div>

  <div class="rule"></div>

  <h3 class="service-title" style="left:69px">Project Management</h3>
  <div class="copy abs" style="left:69px;top:303px;width:241px;text-align:justify">Project Management is one of the most important areas of any business operations, however can often be overlooked. Velmarq Studio can be engaged to help where project management is required but the resources are not available internally. Available for anything from half day reviews to several month projects, Velmarq Studio can be used as an outsourced resource to take out the pain of your project.</div>
  <span class="btn" style="left:69px;top:474px;width:89px">CONTACT US</span>

  <h3 class="service-title" style="left:335px">Business Process Analysis</h3>
  <div class="copy abs" style="left:335px;top:303px;width:241px;text-align:justify">Too often, small businesses spend plenty of time reviewing their market, and analysing competitior behaviour, but without ever taking a look inside their own operations. Velmarq Studio have experience with business reviews, marketing development, profit and loss analysis and much more, and can be engaged on anything from a half day review meeting to several months.</div>
  <span class="btn" style="left:335px;top:474px;width:89px">CONTACT US</span>

  <h3 class="service-title orange" style="left:599px;width:241px">Software Training and Implementation</h3>
  <ul class="service-list">
    <li><span class="chev"></span>Brindlepath</li>
    <li><span class="chev"></span>Fieldora</li>
    <li><span class="chev"></span>Cloudwell Suite</li>
    <li><span class="chev"></span>Stockrise</li>
    <li><span class="chev"></span>Tillbay</li>
  </ul>
</section>

<section class="blog">
  <h2 class="section-title abs" style="left:69px;top:14px">Blog</h2>
  <svg class="blog-arrows" width="25" height="14" viewBox="0 0 25 14"><path d="M7 2L2 7l5 5M17 2l5 5-5 5" fill="none" stroke="#444" stroke-width="2.4"/></svg>
  <div class="blog-image" role="img" aria-label="Glowing cloud icon connected by circuit lines over a world map"></div>
  <h3 class="post-title">Atullam volutpat dui et nisl pharetra, in convallis ipsum</h3>
  <div class="post-meta">July-31-13 &nbsp;:: &nbsp;10.15 a.m</div>
  <p class="copy post-body">Pellentesque at tristique nunc. Nunc quam orci, egestas et tortor et, molestie adipiscing velit. Nunc hendrerit risus ut dui condimentum dignissim. Sed nec mattis augue. Nunc ante eros, eleifend ac odio id, dictum sagittis urna. Praesent eros dolor, condimentum ac laoreet id, laoreet vel sapien. Duis laoreet ac turpis eu molestie. Fusce facilisis nunc at orci congue aliquet.</p>
  <div class="share-row">
    <span class="share-btn"><span></span>Like</span><span class="share-count">3k</span>
    <span class="share-btn" style="color:#222"><span style="background:#6cb6dd"></span>Share</span><span class="share-count">316</span>
  </div>
</section>

<footer class="site-footer">
  <div class="footer-nav">Home<span>|</span>Software Training and Implementation<span>|</span>Project Management<span>|</span>Business Process Analysis<span>|</span>Blog<span>|</span>About Us<span>|</span>Contact Us</div>
  <div class="copyright">Copyright &nbsp;© &nbsp;2013 &nbsp;Velmarq Studio. &nbsp;&nbsp;All rights reserved.</div>
  <div class="social"><i style="background:#3b5a9a"></i><i style="background:#3fa9dd"></i></div>
</footer>

</body>
</html>
```